Executive Business Card for Healthcare Company [Need Today]

I need a business card design for a healthcare company. The only branding the company has thus far is a logo. The cards will be utilized by company executives. The design I envision will be vibrant and appealing but with a corporate feel. They shouldn't be too casual or playful. I would like to complete this project TODAY if possible.

Target Market(s)

Healthcare vendors, other executives in healthcare and pharmaceuticals

Industry/Entity Type

Pharmaceutical

Contact Information for Business Card

See attachment

Font styles to use
Serif
Sans Serif

Colors

Designer to choose colors to be used in the design.

```html
<!DOCTYPE html>
<html lang="en">
<head>
<meta charset="utf-8">
<title>Velora Therapeutics – Business Card</title>
<link href="https://fonts.googleapis.com/css2?family=Roboto:wght@300;400&display=swap" rel="stylesheet">
<style>
  :root {
    --bg: #e9eaec;
    --teal: #25aec2;
    --teal-mid: #3aafaa;
    --green: #52b58c;
    --white: #ffffff;
    --ink: #4a4f55;
    --brand: #2aa6b4;
  }
  * { margin: 0; padding: 0; box-sizing: border-box; }
  html, body {
    width: 1200px; height: 726px; overflow: hidden;
    background: var(--bg);
    font-family: "Roboto", Arial, sans-serif;
  }
  .stage { position: relative; width: 1200px; height: 726px; }
  .card {
    position: absolute; top: 208px;
    width: 540px; height: 309px;
    overflow: hidden;
    box-shadow: 0 2px 6px rgba(0,0,0,.12);
  }

  /* Front */
  .card--front {
    left: 40px;
    background: linear-gradient(180deg, var(--teal) 0%, var(--green) 100%);
    color: var(--white);
  }
  .front-brand {
    position: absolute; left: 0; right: 0; top: 96px;
    display: flex; align-items: center; justify-content: center; gap: 18px;
  }
  .front-brand__circle {
    width: 78px; height: 78px; border-radius: 50%;
    border: 3px solid var(--white);
  }
  .front-brand__divider { width: 1.5px; height: 66px; background: var(--white); }
  .front-brand__name {
    font-weight: 300; font-size: 34px; letter-spacing: 1px; line-height: 1;
  }
  .front-url {
    position: absolute; left: 0; right: 0; top: 236px;
    text-align: center; font-weight: 300; font-size: 14px; letter-spacing: 5px;
  }

  /* Back */
  .card--back { left: 620px; background: var(--white); }
  .back-band {
    position: absolute; inset: 0;
    background: linear-gradient(180deg, var(--teal) 0%, var(--green) 100%);
    clip-path: polygon(0 41%, 62% 41%, 82% 20%, 100% 20%, 100% 78%, 0 78%);
  }
  .back-circle {
    position: absolute; left: 386px; top: 42px;
    width: 138px; height: 138px; border-radius: 50%;
    background: var(--white);
    border: 3px solid var(--white);
    box-shadow: 0 0 0 4px var(--green) inset;
  }
  .back-brand {
    position: absolute; left: 26px; top: 62px;
    font-weight: 300; font-size: 30px; color: var(--brand); line-height: 1;
  }
  .person { position: absolute; left: 40px; top: 140px; color: var(--white); }
  .person__name { font-weight: 400; font-size: 21px; }
  .person__title { font-weight: 300; font-size: 10.5px; margin-top: 3px; opacity: .9; }
  .contacts {
    position: absolute; left: 40px; top: 188px; list-style: none;
    color: var(--white); font-weight: 300; font-size: 13px;
  }
  .contacts li { display: flex; align-items: center; gap: 9px; height: 17px; }
  .contacts svg { width: 11px; height: 11px; fill: var(--white); flex: none; }
  .address {
    position: absolute; left: 40px; top: 264px;
    font-weight: 300; font-size: 13.5px; color: var(--ink);
  }
</style>
</head>
<body>
<main class="stage">
  <section class="card card--front" aria-label="Card front">
    <div class="front-brand">
      <span class="front-brand__circle"></span>
      <span class="front-brand__divider"></span>
      <span class="front-brand__name">Velora Therapeutics</span>
    </div>
    <p class="front-url">www.velorarx.com</p>
  </section>

  <section class="card card--back" aria-label="Card back">
    <div class="back-band"></div>
    <span class="back-circle"></span>
    <p class="back-brand">Velora Therapeutics</p>
    <div class="person">
      <p class="person__name">Daniel Hartley</p>
      <p class="person__title">Senior Director of Marketing</p>
    </div>
    <ul class="contacts">
      <li>
        <svg viewBox="0 0 12 12" aria-hidden="true"><path d="M1 3.5C1 2 2.5 1 6 1s5 1 5 2.5V5H8.5V3.8h-5V5H1zM2.5 6h7l1 5h-9z"/></svg>
        555-201-4837
      </li>
      <li>
        <svg viewBox="0 0 12 12" aria-hidden="true"><path d="M3 0h6v12H3zM4 1.5v8h4v-8zM5.5 10.3h1v.9h-1z" fill-rule="evenodd"/></svg>
        555-318-6042
      </li>
      <li>
        <svg viewBox="0 0 12 12" aria-hidden="true"><circle cx="6" cy="6" r="5.5"/><path d="M0.5 6h11M6 .5c-2.5 3-2.5 8 0 11M6 .5c2.5 3 2.5 8 0 11" stroke="#3aafaa" stroke-width=".9" fill="none"/></svg>
        dhartley@velorarx.com
      </li>
    </ul>
    <p class="address">118 Linden Avenue Marlow, GA 30000</p>
  </section>
</main>
</body>
</html>
```